KVOR Individual and Corporate Development Business Card Design

KVOR needs a business card design that is aligned with it's values and targetted markets. Coherent Lattice of Adaptive Reasoning Method's self diagnosis model and tools, which can be used for personal improvement and team/business performance enhancement, is based on the learnings of over 20 years of medical practitioning. KVOR supercharges personal effectiveness and awareness to also increase team and business performance.

The targetted markets are high performance individuals and teams who aspire seek to enhance their capabilities and achieve their absolute best potential.

Look and feel for the business card design we are looking for is high technology, premium, fresh, new and medical.

Target Market(s)

Industry/Entity Type

Business Consultant

Contact Information for Business Card

Logo, Full Name, Title, Phone number, Email, company name, Address,

Font styles to use
Sans Serif

Requirements
Must have
• Tag line: Sharper Minds, Stronger Teams, Better Outcomes Daily
• Please use same colours as the logo.

```html
<!DOCTYPE html>
<html lang="en">
<head>
<meta charset="utf-8">
<title>KVOR Business Card</title>
<link href="https://fonts.googleapis.com/css2?family=Roboto:ital,wght@0,400;0,500;0,700;1,400&display=swap" rel="stylesheet">
<style>
  :root {
    --backdrop: #2b2b2c;
    --card-front: #f2f2f2;
    --card-back: #5b5e63;
    --teal: #03a7c0;
    --swoosh-grey: #cfcfcf;
    --ink-white: #ffffff;
  }
  * { box-sizing: border-box; margin: 0; padding: 0; }
  html, body {
    width: 1200px; height: 960px; overflow: hidden;
    background: var(--backdrop);
    font-family: "Roboto", Arial, sans-serif;
  }
  .canvas { position: relative; width: 1200px; height: 960px; }
  .card { position: absolute; width: 600px; height: 342px; overflow: hidden; }
  .card--front { left: 314px; top: 113px; background: var(--card-front); }
  .card--back { left: 311px; top: 472px; background: var(--card-back); }

  .card__swoosh { position: absolute; inset: 0; width: 600px; height: 342px; }

  .brand {
    display: flex; align-items: center; gap: 12px;
    font-weight: 700; letter-spacing: 2px; line-height: 1;
  }
  .brand__dot { border-radius: 50%; flex: none; }

  .card--front .brand {
    position: absolute; left: 66px; top: 82px;
    color: var(--teal); font-size: 64px;
  }
  .card--front .brand__dot { width: 22px; height: 22px; background: var(--teal); }

  .contact {
    position: absolute; right: 28px; top: 120px;
    text-align: right; color: var(--ink-white);
  }
  .contact__name { font-size: 20px; font-weight: 700; letter-spacing: 0.2px; line-height: 24px; }
  .contact__title { font-size: 14px; font-weight: 500; line-height: 18px; margin-top: 2px; }
  .contact__company { font-size: 14px; font-weight: 500; line-height: 18px; margin-top: 14px; }
  .contact__address { font-size: 14px; font-weight: 400; line-height: 18px; margin-top: 4px; }
  .contact__lines { list-style: none; margin-top: 8px; font-size: 14px; font-weight: 400; }
  .contact__lines li {
    display: flex; justify-content: flex-end; align-items: center;
    gap: 10px; height: 19.5px;
  }
  .contact__lines svg { width: 14px; height: 14px; fill: var(--ink-white); flex: none; }

  .card--back .brand {
    position: absolute; left: 0; right: 0; top: 130px; justify-content: center;
    color: var(--ink-white); font-size: 64px;
  }
  .card--back .brand__dot { width: 22px; height: 22px; background: var(--ink-white); }
  .tagline {
    position: absolute; left: 0; right: 0; top: 292px; text-align: center;
    color: var(--ink-white); font-size: 14px; font-style: italic; font-weight: 400;
  }
</style>
</head>
<body>
<main class="canvas">

  <section class="card card--front" aria-label="Business card front">
    <svg class="card__swoosh" viewBox="0 0 600 342" aria-hidden="true">
      <path d="M246 342 L424 70 C462 8 528 -4 568 8 C588 16 597 30 600 44 L600 342 Z" fill="var(--swoosh-grey)"/>
      <path d="M258 342 L432 78 C468 22 520 12 556 22 C578 30 594 52 600 78 L600 342 Z" fill="var(--teal)"/>
    </svg>

    <div class="brand">
      <span class="brand__name">KVOR</span>
      <span class="brand__dot"></span>
    </div>

    <div class="contact">
      <p class="contact__name">DANIEL REYES</p>
      <p class="contact__title">CEO/FOUNDER</p>
      <p class="contact__company">Coherent Lattice of Adaptive<br>Reasoning Method</p>
      <p class="contact__address">2140 Harbor View Road<br>Juneau, Alaska 99801</p>
      <ul class="contact__lines">
        <li>555 201 7734
          <svg viewBox="0 0 24 24" aria-hidden="true"><path d="M6.6 10.8a15.1 15.1 0 0 0 6.6 6.6l2.2-2.2a1 1 0 0 1 1-.25 11.4 11.4 0 0 0 3.6.57 1 1 0 0 1 1 1V20a1 1 0 0 1-1 1A17 17 0 0 1 3 4a1 1 0 0 1 1-1h3.5a1 1 0 0 1 1 1c0 1.25.2 2.45.57 3.57a1 1 0 0 1-.25 1z"/></svg>
        </li>
        <li>hello@kvor-method.com
          <svg viewBox="0 0 24 24" aria-hidden="true"><path d="M2 6.5V19h20V6.5l-10 7.5z M2.5 5h19L12 12.2z"/></svg>
        </li>
        <li>www.kvor-method.com
          <svg viewBox="0 0 24 24" aria-hidden="true"><circle cx="12" cy="12" r="10"/><path d="M7 8c2 0 3 1 3 3s-2 2-2 4 1 3 0 4M15 5c-1 2 0 3 2 3s2 3 1 5-3 2-3 4" fill="none" stroke="var(--teal)" stroke-width="1.6"/></svg>
        </li>
      </ul>
    </div>
  </section>

  <section class="card card--back" aria-label="Business card back">
    <div class="brand">
      <span class="brand__name">KVOR</span>
      <span class="brand__dot"></span>
    </div>
    <p class="tagline">Sharper Minds, Stronger Teams, Better Outcomes Daily</p>
  </section>

</main>
</body>
</html>
```